Car transport business

We need a new business card design. Attached is our old card sample. I would just like to adjust the logo colors (blue and red) to be brighter. I changed my name to the brighter red and the word dispatcher to a brighter blue as an example. But you can adjust those colors further. And then perhaps you can use the same colors for the card design but use your imagination.

As a suggestion so the card stands out I would like to add a clip art of car carrier truck. Attached are examples of that as well

```html
<!DOCTYPE html>
<html lang="en">
<head>
<meta charset="utf-8">
<title>Apex Haul – Business Card</title>
<link rel="stylesheet" href="https://fonts.googleapis.com/css2?family=Montserrat:wght@400;500;700;800&display=swap">
<style>
  :root {
    --brand-blue: #1f74c8;
    --brand-red: #e8202a;
    --card-white: #ffffff;
    --card-dark: #2f2f30;
    --ink: #3a3a3a;
    --stage: #1b1b1c;
    --art-dark: #151515;
    --art-mid: #262627;
  }
  * { box-sizing: border-box; margin: 0; padding: 0; }
  html, body {
    width: 1200px; height: 900px; overflow: hidden;
    background: var(--stage);
    font-family: "Montserrat", sans-serif;
  }
  .canvas {
    position: relative; width: 1200px; height: 900px;
    display: flex; flex-direction: column; align-items: center; justify-content: center; gap: 36px;
  }
  .card {
    position: relative; width: 700px; height: 400px; overflow: hidden;
  }

  /* Front */
  .card--front { background: var(--card-white); }
  .brand {
    position: absolute; left: 56px; top: 62px;
    display: flex; align-items: center; gap: 12px;
  }
  .brand__dot { width: 16px; height: 16px; border-radius: 50%; background: var(--brand-blue); }
  .brand__name {
    font-weight: 800; font-size: 38px; letter-spacing: 1px; text-transform: uppercase;
    color: var(--brand-blue); line-height: 1;
  }
  .brand__tagline {
    position: absolute; left: 84px; top: 108px;
    font-size: 11px; font-weight: 500; letter-spacing: 3.2px; text-transform: uppercase;
    color: var(--brand-blue);
  }
  .person {
    position: absolute; right: 50px; top: 178px; text-align: right;
  }
  .person__name {
    font-weight: 800; font-size: 26px; text-transform: uppercase; color: var(--brand-red); line-height: 1.1;
  }
  .person__role { font-size: 18px; font-weight: 500; color: var(--brand-blue); }
  .contacts {
    position: absolute; left: 56px; bottom: 62px; list-style: none;
    font-size: 18px; color: var(--ink); line-height: 1.45;
  }
  .contacts li { display: flex; align-items: center; gap: 12px; }
  .contacts svg { width: 16px; height: 16px; flex: none; }
  .stripe { position: absolute; left: 0; right: 0; bottom: 0; height: 22px; }
  .stripe__blue { position: absolute; left: 0; bottom: 0; width: 62%; height: 12px; background: var(--brand-blue); }
  .stripe__red { position: absolute; right: 0; bottom: 0; width: 38%; height: 22px; background: var(--brand-red); }

  /* Back */
  .card--back { background: var(--card-dark); }
  .truck-art {
    position: absolute; left: 170px; top: 110px; width: 500px; height: 290px;
    background: radial-gradient(ellipse at 50% 60%, var(--art-dark) 0%, var(--art-mid) 70%, var(--card-dark) 100%);
    border-radius: 8px;
  }
  .back-brand {
    position: absolute; left: 190px; top: 92px;
  }
  .back-brand__name {
    font-weight: 800; font-size: 58px; letter-spacing: 2px; text-transform: uppercase;
    color: var(--brand-red); line-height: 1;
  }
  .back-brand__tagline {
    margin-top: 6px; font-size: 15px; font-weight: 500; letter-spacing: 4.4px; text-transform: uppercase;
    color: var(--brand-blue);
  }
</style>
</head>
<body>
<main class="canvas">
  <section class="card card--front">
    <div class="brand">
      <span class="brand__dot"></span>
      <span class="brand__name">Apex Haul</span>
    </div>
    <p class="brand__tagline">The Auto Transport Professionals</p>

    <div class="person">
      <p class="person__name">Ravi Denholm</p>
      <p class="person__role">Dispatcher</p>
    </div>

    <ul class="contacts">
      <li>
        <svg viewBox="0 0 16 16"><path fill="var(--brand-blue)" d="M3.5 1.5l2.5 0.5 1 3-1.6 1.2a8 8 0 0 0 4.4 4.4L11 9l3 1 0.5 2.5-1.8 1.8C7 14 2 9 1.7 3.3z"/></svg>
        555-201-0148
      </li>
      <li>
        <svg viewBox="0 0 16 16"><rect x="4" y="1" width="8" height="14" rx="1.5" fill="none" stroke="var(--brand-blue)" stroke-width="1.6"/><circle cx="8" cy="12.5" r="0.9" fill="var(--brand-blue)"/></svg>
        555-201-0172
      </li>
      <li>
        <svg viewBox="0 0 16 16"><rect x="1" y="3" width="14" height="10" rx="1" fill="var(--brand-blue)"/><path d="M1.5 3.5L8 9l6.5-5.5" fill="none" stroke="#fff" stroke-width="1.3"/></svg>
        apexhaulco@mail.com
      </li>
      <li>
        <svg viewBox="0 0 16 16"><circle cx="8" cy="8" r="7" fill="var(--brand-blue)"/><path d="M1 8h14M8 1c-3 3-3 11 0 14M8 1c3 3 3 11 0 14" fill="none" stroke="#fff" stroke-width="1"/></svg>
        www.apexhaulco.com
      </li>
    </ul>

    <div class="stripe">
      <span class="stripe__blue"></span>
      <span class="stripe__red"></span>
    </div>
  </section>

  <section class="card card--back">
    <div class="truck-art" role="img" aria-label="Dark silhouette illustration of a car carrier truck"></div>
    <div class="back-brand">
      <p class="back-brand__name">Apex Haul</p>
      <p class="back-brand__tagline">The Auto Transport Professionals</p>
    </div>
  </section>
</main>
</body>
</html>
```